Plumbing & Heating company

A leaflet containing -

Company name - Larkfield Plumbing Solutions
logo
Mobile number - 07700 914062
Landline - 01632 870215
Email - Info@larkfieldplumbing.example
website - Larkfield-plumbing.example
Social media logos - insta, Facebook

services we offer

- Boiler replacements (free quote)
- General plumbing & heating
- Tap replacements
- 1st & 2nd
- New builds & Extensions
- Cylinder replcemets

```html
<!DOCTYPE html>
<html lang="en">
<head>
<meta charset="utf-8">
<title>Larkfield Plumbing Solutions – Leaflet</title>
<link rel="stylesheet" href="https://fonts.googleapis.com/css2?family=Montserrat:wght@500;600;700;800;900&family=Oswald:wght@500;600&display=swap">
<style>
  :root {
    --bg: #d9dadc;
    --white: #ffffff;
    --off-white: #f1f2f3;
    --navy: #12305e;
    --navy-deep: #0b1f44;
    --blue: #2b7cc4;
    --sky: #3fa6d8;
    --orange: #e8742a;
    --orange-deep: #d4601b;
    --grey-dark: #3e4145;
    --grey-mid: #6d7075;
    --grey-light: #a9acb0;
    --charcoal: #2b2e33;
    --ink: #141414;
  }
  * { box-sizing: border-box; margin: 0; padding: 0; }
  html, body {
    width: 1200px; height: 900px; overflow: hidden;
    background: var(--bg);
    font-family: "Montserrat", sans-serif;
  }
  .leaflet {
    position: absolute; left: 296px; top: 20px;
    width: 608px; height: 860px;
    background: var(--white);
    overflow: hidden;
    box-shadow: 0 8px 24px rgba(0,0,0,.18);
  }
  .layer { position: absolute; }

  /* Header */
  .brand {
    left: 28px; top: 70px; width: 230px;
    display: flex; align-items: center; gap: 10px;
  }
  .brand-mark {
    width: 34px; height: 34px; border-radius: 50%;
    background: var(--blue); flex: none;
  }
  .brand-name {
    font-weight: 800; font-size: 19px; line-height: 1.05;
    color: var(--navy); text-transform: uppercase;
  }

  .hero-photo { left: 0; top: 0; width: 608px; height: 360px; }

  /* Headline band */
  .headline { left: 34px; top: 196px; color: var(--white); }
  .headline-lead {
    font-weight: 700; font-size: 38px; letter-spacing: .5px;
    color: #dfe3e8; line-height: 1;
  }
  .headline-sub {
    font-weight: 700; font-size: 17px; letter-spacing: .5px;
    color: #dfe3e8; margin-top: 6px;
  }
  .headline-tag {
    display: inline-block; margin-top: 10px;
    background: var(--orange); color: var(--white);
    font-weight: 600; font-size: 17px; letter-spacing: 1px;
    padding: 5px 20px;
  }

  .work-tile { top: 330px; height: 116px; }
  .tile-cylinder { left: 30px; width: 130px; background: linear-gradient(160deg, #f0f1f2, #b9bcbf); }
  .tile-boiler { left: 166px; width: 130px; background: linear-gradient(160deg, #d9b98e, #9f7a50); }
  .tile-pipework { left: 302px; width: 150px; background: linear-gradient(160deg, #c6a589, #7c5b45); }

  /* Services */
  .services-title {
    left: 30px; top: 456px; height: 44px; width: 240px;
    background: linear-gradient(180deg, #8e9196, #55585d);
    color: var(--white);
    font-family: "Oswald", sans-serif; font-weight: 600;
    font-size: 26px; letter-spacing: .5px;
    display: flex; align-items: center; justify-content: center;
    border: 2px solid #c9cbce;
  }
  .service-list { list-style: none; }
  .service-list.col-a { left: 34px; top: 514px; width: 260px; }
  .service-list.col-b { left: 318px; top: 470px; width: 270px; }
  .service-list li {
    display: flex; align-items: center; gap: 10px;
    color: var(--white); font-weight: 600; font-size: 12.5px;
    text-transform: uppercase; letter-spacing: .3px;
    padding: 6px 0;
    border-bottom: 1px solid rgba(255,255,255,.28);
    min-height: 38px;
  }
  .service-list li:last-child { border-bottom: none; }
  .service-icon {
    width: 28px; height: 28px; border-radius: 50%; flex: none;
    background: var(--ink); border: 2px solid var(--grey-light);
    display: flex; align-items: center; justify-content: center;
  }
  .service-icon span {
    width: 10px; height: 10px; border-radius: 50%;
    background: var(--orange);
  }

  /* Contact */
  .call-heading { left: 30px; top: 700px; line-height: .95; }
  .call-heading .give { color: var(--orange); font-weight: 800; font-size: 28px; }
  .call-heading .call { color: var(--grey-dark); font-weight: 900; font-size: 38px; }

  .contact-line { display: flex; align-items: center; gap: 10px; }
  .contact-mobile { left: 210px; top: 700px; }
  .contact-landline { left: 398px; top: 650px; }
  .phone-badge {
    width: 40px; height: 40px; border-radius: 50%;
    background: var(--white); border: 3px solid var(--blue);
    display: flex; align-items: center; justify-content: center; flex: none;
  }
  .contact-label { font-weight: 800; font-size: 17px; color: var(--ink); line-height: 1; }
  .contact-number {
    margin-top: 3px; display: inline-block;
    background: var(--orange); color: var(--white);
    font-weight: 800; font-size: 16px;
    padding: 5px 12px; border-radius: 16px;
  }

  .social { left: 456px; top: 735px; display: flex; gap: 14px; }
  .social-dot {
    width: 38px; height: 38px; border-radius: 50%;
    background: var(--blue); border: 3px solid var(--white);
    box-shadow: 0 0 0 2px var(--blue);
  }

  .footer-bar {
    left: 0; top: 792px; width: 608px; height: 44px;
    background: var(--orange);
    display: flex; align-items: center; justify-content: space-between;
    padding: 0 20px;
  }
  .footer-item { display: flex; align-items: center; gap: 8px; color: var(--white); font-weight: 600; font-size: 12.5px; }
  .footer-icon {
    width: 26px; height: 26px; border-radius: 50%;
    background: var(--charcoal); border: 2px solid var(--white);
    display: flex; align-items: center; justify-content: center;
  }
  .footer-strip { left: 0; top: 836px; width: 608px; height: 24px; background: var(--charcoal); }
</style>
</head>
<body>
<main class="leaflet">
  <svg class="layer" width="608" height="860" viewBox="0 0 608 860" aria-hidden="true">
    <defs>
      <linearGradient id="bandNavy" x1="0" y1="0" x2="1" y2="1">
        <stop offset="0" stop-color="#1c4a86"/>
        <stop offset="1" stop-color="#0b1f44"/>
      </linearGradient>
      <linearGradient id="bandGrey" x1="0" y1="0" x2="0" y2="1">
        <stop offset="0" stop-color="#7b7e83"/>
        <stop offset="1" stop-color="#4a4d52"/>
      </linearGradient>
    </defs>
    <path d="M0 190 L608 110 L608 470 L0 470 Z" fill="url(#bandNavy)"/>
    <path d="M0 184 L608 104 L608 110 L0 190 Z" fill="var(--blue)"/>
    <path d="M0 470 L608 430 L608 640 L0 690 Z" fill="url(#bandGrey)"/>
    <path d="M0 690 L608 640 L608 792 L0 792 Z" fill="var(--off-white)"/>
  </svg>

  <div class="layer hero-photo" role="img" aria-label="Photo of a plumber holding hoses and a tool bag in a plant room">
    <svg width="608" height="360" viewBox="0 0 608 360">
      <defs>
        <linearGradient id="heroTone" x1="0" y1="0" x2="1" y2="1">
          <stop offset="0" stop-color="#c9ccd0"/>
          <stop offset=".6" stop-color="#5b7398"/>
          <stop offset="1" stop-color="#314a72"/>
        </linearGradient>
      </defs>
      <path d="M250 0 L608 0 L608 330 L430 345 C330 330 250 240 250 120 Z" fill="url(#heroTone)"/>
      <path d="M250 0 L250 120 C250 240 330 330 430 345" fill="none" stroke="var(--blue)" stroke-width="5"/>
    </svg>
  </div>

  <div class="layer brand">
    <span class="brand-mark"></span>
    <span class="brand-name">Larkfield Plumbing Solutions</span>
  </div>

  <div class="layer headline">
    <div class="headline-lead">ALL YOUR</div>
    <div class="headline-sub">PLUMBING &amp; HEATING</div>
    <div class="headline-tag">SOLUTIONS</div>
  </div>

  <div class="layer work-tile tile-cylinder" role="img" aria-label="Photo of an installed hot water cylinder"></div>
  <div class="layer work-tile tile-boiler" role="img" aria-label="Photo of a wall-mounted boiler with pipework"></div>
  <div class="layer work-tile tile-pipework" role="img" aria-label="Photo of copper pipework in a wall frame"></div>

  <div class="layer services-title">SERVICES WE OFFER</div>

  <ul class="layer service-list col-a">
    <li><span class="service-icon"><span></span></span>Boiler replacements<br>(free quote)</li>
    <li><span class="service-icon"><span></span></span>General plumbing &amp; heating</li>
    <li><span class="service-icon"><span></span></span>Tap replacements</li>
  </ul>
  <ul class="layer service-list col-b">
    <li><span class="service-icon"><span></span></span>1st &amp; 2nd</li>
    <li><span class="service-icon"><span></span></span>New builds &amp; extensions</li>
    <li><span class="service-icon"><span></span></span>Cylinder replcemets</li>
  </ul>

  <div class="layer call-heading">
    <div class="give">GIVE US</div>
    <div class="call">A CALL</div>
  </div>

  <div class="layer contact-line contact-mobile">
    <span class="phone-badge">
      <svg width="18" height="18" viewBox="0 0 24 24"><path d="M6.6 10.8a15 15 0 0 0 6.6 6.6l2.2-2.2a1 1 0 0 1 1-.25 11.4 11.4 0 0 0 3.6.57 1 1 0 0 1 1 1V20a1 1 0 0 1-1 1A17 17 0 0 1 3 4a1 1 0 0 1 1-1h3.5a1 1 0 0 1 1 1c0 1.250.2 2.450.57 3.57a1 1 0 0 1-.25 1z" fill="var(--blue)"/></svg>
    </span>
    <div>
      <div class="contact-label">Mobile</div>
      <span class="contact-number">07700 914062</span>
    </div>
  </div>

  <div class="layer contact-line contact-landline">
    <span class="phone-badge">
      <svg width="18" height="18" viewBox="0 0 24 24"><path d="M6.6 10.8a15 15 0 0 0 6.6 6.6l2.2-2.2a1 1 0 0 1 1-.25 11.4 11.4 0 0 0 3.6.57 1 1 0 0 1 1 1V20a1 1 0 0 1-1 1A17 17 0 0 1 3 4a1 1 0 0 1 1-1h3.5a1 1 0 0 1 1 1c0 1.250.2 2.450.57 3.57a1 1 0 0 1-.25 1z" fill="var(--blue)"/></svg>
    </span>
    <div>
      <div class="contact-label">Landline</div>
      <span class="contact-number">01632 870215</span>
    </div>
  </div>

  <div class="layer social" aria-label="Social media">
    <span class="social-dot"></span>
    <span class="social-dot"></span>
  </div>

  <div class="layer footer-bar">
    <div class="footer-item">
      <span class="footer-icon"><svg width="12" height="12" viewBox="0 0 24 24"><circle cx="12" cy="12" r="9" fill="none" stroke="#fff" stroke-width="2"/><path d="M3 12h18M12 3c3 3 3 15 0 18M12 3c-3 3-3 15 0 18" fill="none" stroke="#fff" stroke-width="1.6"/></svg></span>
      Info@larkfieldplumbing.example
    </div>
    <div class="footer-item">
      <span class="footer-icon"><svg width="12" height="12" viewBox="0 0 24 24"><rect x="3" y="6" width="18" height="12" fill="none" stroke="#fff" stroke-width="2"/><path d="M3 6l9 7 9-7" fill="none" stroke="#fff" stroke-width="2"/></svg></span>
      Larkfield-plumbing.example
    </div>
  </div>
  <div class="layer footer-strip"></div>
</main>
</body>
</html>
```